Creative Web Design for an ERP (technology) Consulting Business

I need two pages designed for the ERP Project Management Consulting Company I am starting. One page is the home page, the other page is an important inside page.

I've looked at many different templates for sites like this, and they all look the same to me. I am working with PixelGuild designers because I want something unique.

This site will be implemented with Wordpress using the Elementor framework,

About Me ---
I have worked with PixelGuild several times before, and I have tired to do everything I can to ve helpful. In the uploads, you will find PDF's with wireframes outlning the layout of the pages, as well as explanatios for each section. There are Word documents that you can copy into text. The list below explains the files included.

Although the wireframes suggest a layout, please feel free to use your creativity - often, I find that the designs I like the most are designs I have never thought of.

About the Company --
ERP (Enterprise Resource Planning) systems are business computer systems that tie different businesss functions together. These systems are expensive and complicated, and efforts to implement them often fail. The purpose of the company is to increase the chance of success by focusing on the things that need to be right.

I have uploaded several files to help clarify what I am looking for:
• 1a - Home Page Wireframe - PDF
Wireframe for the home page with an explanation of each section.
• 1b - Home Page Text – Word
A Word document so that you can copy the text.
• 2 - Copper Harbor Logo – ZIP
Four different versions of the company logo in Adobe Illustrator, PNG, and JPG formats. Any of the four are acceptable:
1. Logo_1 – Black on Transparent – Same Line ERP
2. Logo_2 – White on Transparent – Same Line ERP
3. Logo_3 – Black on Transparent – Big ERP on Different Line
4. Logo_4 – White on Transparent – Big ERP on Different Line
• 3a - Copper Harbor Page Wireframe – PDF
Wireframe for he Copper Harbor page, with explanations and a detailed breakdown of the top section.
• 3b - Copper Harbor Text – Word
• 4 - Colors and Palettes – PDF
• 5 - Change Management Icon – EPS
• 6 – Site Map
If you wish to see it, the site map provides an idea of the entire site. The two pages circled in red are the ones I need to be designed.

Thank you for your interest in this project!

Target Market(s)

Corporate decision makers, primarily CIOs and CFOs, as well as ERP project managers and influencers.

Industry/Entity Type

Consulting

Number of Pages Required

2 page

Font styles to use
Sans Serif

Requirements
Must have
• Pages that contain the elements explained on the wireframes provided.
Nice to have
• A design that looks and feels unique
Should not have
• A typical, template layour

```html
<!DOCTYPE html>
<html lang="en">
<head>
<meta charset="utf-8">
<title>Copper Harbor – The Adaptive 8 Method</title>
<link href="https://fonts.googleapis.com/css2?family=Inter:wght@400;500;600&display=swap" rel="stylesheet">
<style>
  :root {
    --bg: #e5e4f0;
    --ink: #17171b;
    --muted: #55555f;
    --faint: #8a8a96;
    --button: #232327;
    --rule: #b9b8c8;
    --panel: #fbfbfd;
    --steel: #7398b5;
    --lilac: #8f89b8;
    --coral: #e1634a;
    --amber: #e0a74c;
    --white: #ffffff;
  }
  * { box-sizing: border-box; margin: 0; padding: 0; }
  html, body { width: 673px; height: 1200px; overflow: hidden; }
  body {
    font-family: "Inter", Arial, sans-serif;
    background: var(--bg);
    color: var(--ink);
    position: relative;
  }
  .site-header {
    position: absolute; left: 28px; right: 28px; top: 0; height: 53px;
    border-bottom: 1px solid var(--rule);
  }
  .brand { position: absolute; left: 0; top: 17px; display: flex; align-items: center; gap: 6px; font-weight: 600; font-size: 14px; letter-spacing: -0.2px; }
  .brand-dot { width: 9px; height: 9px; border-radius: 50%; background: var(--coral); }
  .nav-link { position: absolute; top: 20px; font-size: 10px; color: var(--ink); }
  .search { position: absolute; left: 503px; top: 20px; }
  .header-cta {
    position: absolute; right: -5px; top: 8px;
    background: var(--button); color: var(--white);
    font-size: 10px; height: 34px; width: 78px; border-radius: 17px;
    display: flex; align-items: center; justify-content: center;
  }
  .btn {
    position: absolute; background: var(--button); color: var(--white);
    font-size: 10.5px; font-weight: 500; width: 113px; height: 41px; border-radius: 21px;
    display: flex; align-items: center; justify-content: center;
  }
  .hero-title {
    position: absolute; top: 106px; left: 0; width: 673px; text-align: center;
    font-size: 34px; font-weight: 600; line-height: 43px; letter-spacing: -0.8px;
  }
  .hero-lead {
    position: absolute; top: 205px; left: 0; width: 673px; text-align: center;
    font-size: 11px; line-height: 17px; color: var(--ink);
  }
  .band-rule { position: absolute; left: 0; width: 673px; height: 1px; background: var(--rule); top: 336px; }
  .tile { position: absolute; width: 168px; height: 149px; display: flex; align-items: center; justify-content: center; }
  .eyebrow { position: absolute; font-size: 6.5px; letter-spacing: 0.6px; color: var(--faint); text-transform: uppercase; }
  .block-title { position: absolute; font-weight: 500; letter-spacing: -0.4px; }
  .block-copy { position: absolute; font-size: 9.5px; line-height: 14.5px; color: var(--muted); }
  .panel-white { position: absolute; left: 337px; top: 633px; width: 336px; height: 297px; background: var(--panel); }
  .closing-title {
    position: absolute; top: 1026px; left: 0; width: 673px; text-align: center;
    font-size: 21.5px; line-height: 28px; font-weight: 400; letter-spacing: -0.4px;
  }
</style>
</head>
<body>

<header class="site-header">
  <div class="brand"><span class="brand-dot"></span>Copper Harbor</div>
  <nav>
    <span class="nav-link" style="left:208px;">Home</span>
    <span class="nav-link" style="left:258px;">Method</span>
    <span class="nav-link" style="left:318px;">Services</span>
    <span class="nav-link" style="left:380px;">About</span>
    <span class="nav-link" style="left:434px;">Blog</span>
  </nav>
  <svg class="search" width="12" height="12" viewBox="0 0 12 12" fill="none" stroke="#17171b" stroke-width="1.4"><circle cx="5" cy="5" r="3.6"/><path d="M7.7 7.7 11 11"/></svg>
  <div class="header-cta">Contact</div>
</header>

<h1 class="hero-title">The Adaptive 8 Method<br>for ERP success.</h1>
<p class="hero-lead">A framework grouping critical success factors into high level categories<br>so every ERP project stays focused.</p>
<a class="btn" style="left:280px;top:254px;">Learn more</a>

<div class="band-rule"></div>

<section>
  <p class="eyebrow" style="left:29px;top:397px;">Our framework · More</p>
  <h2 class="block-title" style="left:29px;top:427px;font-size:18px;line-height:24px;">Framework grouping success<br>factors for ERP success.</h2>
  <p class="block-copy" style="left:29px;top:485px;">A focused set of categories that guide every<br>decision across planning, people and systems<br>to keep projects on track.</p>
  <a class="btn" style="left:29px;top:545px;">Learn more</a>

  <div class="tile" style="left:337px;top:336px;background:var(--steel);">
    <svg width="44" height="44" viewBox="0 0 44 44" fill="none" stroke="#fff" stroke-width="6" stroke-linecap="round" stroke-linejoin="round"><path d="M8 23l9 9 19-19"/></svg>
  </div>
  <div class="tile" role="img" aria-label="Photo of a glass office tower against the sky" style="left:505px;top:336px;background:linear-gradient(150deg,#a9bfd6,#3e5a80 60%,#1e3050);"></div>
  <div class="tile" role="img" aria-label="Photo of tall wooden architectural slats" style="left:337px;top:485px;background:linear-gradient(90deg,#cdb89a,#8d7558 45%,#d8c6aa 70%,#9a8264);"></div>
  <div class="tile" style="left:505px;top:485px;background:var(--lilac);">
    <svg width="44" height="44" viewBox="0 0 44 44" fill="none" stroke="#fff" stroke-width="5" stroke-linecap="round"><circle cx="22" cy="22" r="17"/><path d="M22 14v16M14 22h16"/></svg>
  </div>
</section>

<section>
  <div class="tile" style="left:0;top:633px;background:var(--coral);">
    <svg width="58" height="40" viewBox="0 0 58 40" fill="none" stroke="#fff" stroke-width="6" stroke-linejoin="round"><path d="M2 20h48M34 4l16 16-16 16"/></svg>
  </div>
  <div class="tile" role="img" aria-label="Photo of a glass curtain-wall office facade" style="left:168px;top:633px;background:linear-gradient(160deg,#b9cde2,#3d5778 55%,#22344e);"></div>
  <div class="tile" role="img" aria-label="Photo of a modern office building entrance with trees" style="left:0;top:782px;background:linear-gradient(180deg,#c8d0da,#6b7684 55%,#3f4a3d);"></div>
  <div class="tile" style="left:168px;top:782px;background:var(--amber);">
    <svg width="44" height="54" viewBox="0 0 44 54"><path d="M4 50V20h26V4h4v8h4v38z" fill="#fff"/><path d="M4 50 30 22v28z" fill="#f0cf93"/></svg>
  </div>

  <div class="panel-white"></div>
  <p class="eyebrow" style="left:369px;top:693px;">Our approach · More</p>
  <h2 class="block-title" style="left:369px;top:724px;font-size:15.5px;line-height:22px;">The adaptive approach combining<br>for ERP project execution.</h2>
  <p class="block-copy" style="left:369px;top:780px;">Structured planning sets the course while short<br>agile cycles keep delivery responsive, visible<br>and aligned with goals.</p>
  <a class="btn" style="left:370px;top:838px;">Learn more</a>
</section>

<section>
  <svg style="position:absolute;left:324px;top:993px;" width="25" height="24" viewBox="0 0 25 24" fill="none" stroke="#e1634a" stroke-width="1.8" stroke-linejoin="round"><path d="M2 9 12.5 2 23 9v13H2z"/><path d="M2 9l10.5 7L23 9"/></svg>
  <h2 class="closing-title">A flexible approach combining<br>waterfall planning with agile<br>execution.</h2>
  <a class="btn" style="left:280px;top:1129px;">Learn more</a>
</section>

</body>
</html>
```